Wordpress website for a new Podcast

Hi, We are looking for a designer to create a wordpress website project for a new podcast and publish it on the domain we own.

The show is called “Bright Gatherings” (logo included) and its aim is to interview guests who work as professional facilitators, trainers, teachers and coaches. The show has a positive vibe, is fun, vibrant and full of positive energy. These are the feelings we want to convey in the design.

The website should have a similar structure to: https://www.plumvesselcast.example/ with the following content:

1) The main page including:
- navigation bar and social buttons at the top
- main graphic design featuring the latest episode
- "latest episodes" section displaying 3 episodes (please design a mask to be used for new episodes when they air together with the face of the interviewee) -> this will link to the respective episodes
- please design an "bright gatherings" book cover mockup to be inluded as a banner -> this will link to Orindel
- subscribe to the newsletter - a banner capturing the name and email of the user -> to be connected to PostWren.
-> a working episode search.

2) Episodes page
- the show will be divided into seasons (12 episodes each) and each episode will need a separate "blog entry" including:
-> A short article (4-5 paragraphs) + stock image
-> interviewee's bio and social links

3) Meet the hosts page
- including bios of the two hosts of the show
- links to their social profiles
- a "request speaker availability" form which sends an email

Some additional nice-to-haves:
1) Good and clean Bio's would be awesome (both for the hosts & the interviewees),
2) an easily navigable episode system,
3) a keyword/date search option
4) easy to share options (share to WhatsApp, Facebook, Twitter, LinkedIn) 5) We must be able to track how the podcasts are shared (google analytics?)

```html
<!DOCTYPE html>
<html lang="en">
<head>
<meta charset="utf-8">
<title>Bright Gatherings</title>
<link rel="stylesheet" href="https://fonts.googleapis.com/css2?family=Mulish:wght@400;600;700;800&display=swap">
<style>
:root{
  --orange:#f15a0f;
  --orange-deep:#e44a06;
  --orange-light:#ffa21c;
  --ink:#1d1d1d;
  --text:#333;
  --grey-bg:#efefef;
  --footer:#2b2b2b;
  --white:#fff;
}
*{box-sizing:border-box;margin:0;padding:0}
html,body{width:1200px;height:4201px;overflow:hidden}
body{position:relative;background:var(--white);font-family:"Mulish",sans-serif;color:var(--text)}
.abs{position:absolute}
a{color:inherit;text-decoration:none}

/* header */
.social-dots{left:212px;top:38px;display:flex;gap:22px}
.social-dots span{width:16px;height:16px;border-radius:50%;background:var(--ink)}
.brand-badge{left:535px;top:0;width:130px;height:130px;border-radius:50%;
  background:var(--orange);
  display:flex;align-items:center;justify-content:center;text-align:center;
  color:var(--white);font-weight:800;font-size:17px;line-height:1.1;letter-spacing:.5px;z-index:3}
.search{left:774px;top:24px;width:246px;height:44px;border:1px solid #e2e2e2;border-radius:22px;
  font-size:13px;color:#999;padding:13px 18px}
.search-btn{right:4px;top:6px;width:32px;height:32px;border-radius:50%;background:var(--orange)}
.header-rule{left:0;top:86px;width:1200px;height:1px;background:#e6e6e6}
.nav{top:99px;font-size:15px;font-weight:600;color:var(--ink)}
.nav a{position:absolute;white-space:nowrap}

/* hero */
.hero{left:0;top:134px;width:1200px;height:608px;
  background:linear-gradient(100deg,#e9e3dd 0%,#d8d0c8 55%,#c9c0b7 100%)}
.hero-book{left:147px;top:78px;width:318px;height:448px;
  background:linear-gradient(90deg,var(--orange) 0 62%,#d9d6d2 62% 100%);box-shadow:12px 20px 30px rgba(0,0,0,.25)}
.hero-title{left:662px;top:176px;font-size:58px;font-weight:400;color:var(--ink);white-space:nowrap}
.hero-copy{left:662px;top:248px;width:440px;font-size:16px;line-height:36px;text-align:justify;color:#333}
.hero-edge{left:0;top:742px;width:1200px;height:6px;background:var(--orange)}
.btn{display:flex;align-items:center;justify-content:center;gap:10px;border-radius:30px;
  color:var(--white);font-weight:600;white-space:nowrap}
.btn .arrow{width:18px;height:18px;border-radius:50%;background:var(--white);position:relative}
.btn .arrow::after{content:"";position:absolute;left:6px;top:5px;border-left:7px solid var(--orange);
  border-top:4px solid transparent;border-bottom:4px solid transparent}
.btn.dark .arrow::after{border-left-color:var(--ink)}
.btn-orange{background:var(--orange)}
.btn.dark{background:#1c1c1c}

/* welcome */
.center{left:0;width:1200px;text-align:center}
.welcome-small{top:838px;font-size:21px;color:var(--ink)}
.section-title{font-size:36px;color:var(--orange);font-weight:400}
.welcome-copy{top:922px;left:140px;width:920px;font-size:15px;line-height:36px}
.field{top:1022px;width:226px;height:42px;background:var(--white);box-shadow:0 2px 6px rgba(0,0,0,.15);
  font-size:13px;padding:13px 10px;color:#555}
.field i{position:absolute;right:12px;top:15px;width:11px;height:11px;background:var(--orange);border-radius:2px}
.subscribe{left:870px;top:1022px;width:225px;height:42px;background:var(--orange);color:var(--white);
  font-size:17px;font-weight:600;display:flex;align-items:center;justify-content:center;box-shadow:0 2px 6px rgba(0,0,0,.2)}
.rule{left:90px;top:1154px;width:1020px;height:1px;background:#cfcfcf}

/* about */
.about-ring{left:80px;top:1243px;width:444px;height:444px;border-radius:50%;border:4px solid var(--orange);
  border-left-color:transparent;border-bottom-color:transparent;transform:rotate(-20deg)}
.about-photo{left:90px;top:1267px;width:424px;height:424px;border-radius:50%;
  background:radial-gradient(circle at 50% 40%,#3a3a3a,#141414 75%)}
.about-title{left:567px;top:1295px;font-size:36px;color:var(--orange);font-weight:400}
.about-copy{left:567px;top:1351px;width:536px;font-size:15px;line-height:34px;text-align:justify}

/* podcasts */
.podcasts{left:0;top:1777px;width:1200px;height:561px;background:var(--grey-bg)}
.card{top:148px;width:328px}
.card-img{width:328px;height:194px}
.card-icon{left:146px;top:176px;width:36px;height:36px;border-radius:50%;background:var(--orange);border:3px solid var(--white)}
.card-title{top:226px;width:328px;text-align:center;color:var(--orange);font-size:17px;font-weight:400}
.card-copy{top:256px;left:40px;width:248px;text-align:center;font-size:13px;line-height:26px}
.card-more{top:314px;width:328px;text-align:center;color:var(--orange);font-size:14px}

/* banner */
.banner{left:0;top:2338px;width:1200px;height:384px;
  background:linear-gradient(90deg,#1a1614 0%,#3b3029 40%,#8b7666 70%,#5e5048 100%)}
.banner-title{left:90px;top:82px;font-size:34px;color:var(--white);font-weight:600}
.banner-copy{left:90px;top:132px;width:490px;font-size:15px;line-height:31px;color:var(--white);text-align:justify}

/* book promo */
.promo-name{top:2830px;font-size:58px;font-weight:800;color:var(--orange);line-height:70px;letter-spacing:2px}
.promo-copy{top:2932px;left:170px;width:860px;font-size:15px;line-height:33px}
.orbit{left:323px;top:3126px;width:554px;height:554px;border-radius:50%;border:1px dashed #f39a70}
.core{left:401px;top:3204px;width:398px;height:398px;border-radius:50%;
  background:radial-gradient(circle at 50% 50%,#ff8a1e 0%,var(--orange) 55%,var(--orange-deep) 100%);
  box-shadow:0 0 0 10px rgba(241,90,15,.15)}
.core-book{left:108px;top:98px;width:166px;height:200px;
  background:linear-gradient(90deg,#f7941d 0 58%,#e8e4df 58% 100%);box-shadow:10px 14px 20px rgba(0,0,0,.3)}
.feature{width:120px;height:120px;border-radius:50%;background:var(--orange);box-shadow:0 0 0 8px rgba(241,90,15,.2);
  display:flex;align-items:center;justify-content:center}
.feature-label{width:220px;text-align:center;font-size:26px;line-height:36px;color:var(--ink)}
.feature-label span{display:block;color:var(--orange)}

/* footer */
.footer-edge{left:0;top:3782px;width:1200px;height:8px;background:var(--orange)}
.footer{left:0;top:3790px;width:1200px;height:411px;background:var(--footer)}
.footer-name{top:100px;font-size:30px;font-weight:800;color:var(--white);letter-spacing:2px}
.footer-dots{left:530px;top:268px;display:flex;gap:6px}
.footer-dots span{width:28px;height:28px;border-radius:50%;border:2px solid var(--white)}
.footer-links{top:318px;font-size:17px;color:var(--white)}
.copyright{top:356px;font-size:15px;color:var(--white);letter-spacing:1px}
</style>
</head>
<body>

<header>
  <div class="abs social-dots" aria-label="Social profiles"><span></span><span></span><span></span><span></span><span></span></div>
  <div class="abs brand-badge">Bright<br>Gatherings</div>
  <div class="abs search">Search<span class="abs search-btn"></span></div>
  <div class="abs header-rule"></div>
  <nav class="abs nav" style="left:0;width:1200px">
    <a style="left:126px">Home</a>
    <a style="left:202px">About Us</a>
    <a style="left:305px">Our Blog</a>
    <a style="left:404px">Podcasts</a>
    <a style="left:728px">Training</a>
    <a style="left:821px">Free Stuff</a>
    <a style="left:927px">Webinars</a>
    <a style="left:1032px">Shop</a>
  </nav>
</header>

<section class="abs hero">
  <div class="abs hero-book" role="img" aria-label="Bright Gatherings book cover mockup standing open"></div>
  <h1 class="abs hero-title">Bright Gathering</h1>
  <p class="abs hero-copy">Lorem ipsum dolor sit amet, consectetur adipiscing elit, sed do eiusmod tempor incididunt ut labore et dolore magna aliqua.</p>
  <a class="abs btn btn-orange" style="left:662px;top:363px;width:233px;height:56px;font-size:19px">Get the Book Now <span class="arrow"></span></a>
  <a class="abs btn dark" style="left:905px;top:363px;width:205px;height:56px;font-size:19px">Get Trained <span class="arrow"></span></a>
</section>
<div class="abs hero-edge"></div>

<section>
  <p class="abs center welcome-small">Welcome to</p>
  <h2 class="abs center section-title" style="top:866px">Bright Gatherings</h2>
  <p class="abs welcome-copy" style="text-align:center">Sed ut perspiciatis unde omnis iste natus error sit voluptatem accusantium doloremque laudantium, totam rem aperiam, eaque ipsa quae ab illo inventore veritatis et quasi architecto beatae vitae dicta sunt explicabo.</p>
  <div class="abs field" style="left:103px">Full Name<i></i></div>
  <div class="abs field" style="left:359px">Phone Number<i></i></div>
  <div class="abs field" style="left:614px">Email Address<i></i></div>
  <a class="abs subscribe">&#10148;&nbsp;Subscribe</a>
  <div class="abs rule"></div>
</section>

<section>
  <div class="abs about-ring"></div>
  <div class="abs about-photo" role="img" aria-label="Video still of a speaker addressing a large audience, seen from behind"></div>
  <h2 class="abs about-title">About Us</h2>
  <p class="abs about-copy">Sed ut perspiciatis unde omnis iste natus error sit voluptatem accusantium doloremque laudantium, totam rem aperiam, eaque ipsa quae ab illo inventore veritatis et quasi architecto beatae vitae dicta sunt explicabo. Nemo enim ipsam voluptatem quia voluptas sit aspernatur aut odit aut fugit, sed quia consequuntur magni dolores eos qui ratione voluptatem sequi nesciunt.</p>
  <a class="abs btn btn-orange" style="left:567px;top:1576px;width:206px;height:52px;font-size:19px">Get Trained <span class="arrow"></span></a>
</section>

<section class="abs podcasts">
  <h2 class="abs center section-title" style="top:80px">Latest Podcast Episodes</h2>
  <article class="abs card" style="left:88px">
    <div class="card-img" role="img" aria-label="Episode photo of a trainer presenting to a seated group" style="background:linear-gradient(160deg,#6b6f76,#2e3036)"></div>
    <span class="abs card-icon"></span>
    <h3 class="abs card-title">SED UT PERSPICIATIS UND</h3>
    <p class="abs card-copy">Sed ut perspiciatis unde omnis iste natus error sit voluptatem tium</p>
    <a class="abs card-more">READ MORE</a>
  </article>
  <article class="abs card" style="left:435px">
    <div class="card-img" role="img" aria-label="Episode photo of a speaker on stage before a cheering crowd" style="background:linear-gradient(180deg,#3a3331,#7b5a46)"></div>
    <span class="abs card-icon"></span>
    <h3 class="abs card-title">SED UT PERSPICIATIS UND</h3>
    <p class="abs card-copy">Sed ut perspiciatis unde omnis iste natus error sit voluptatem tium</p>
    <a class="abs card-more">READ MORE</a>
  </article>
  <article class="abs card" style="left:782px">
    <div class="card-img" role="img" aria-label="Episode photo of a guest speaker with a headset microphone" style="background:linear-gradient(90deg,#e6a3e0,#f3d6ef)"></div>
    <span class="abs card-icon"></span>
    <h3 class="abs card-title">SED UT PERSPICIATIS UND</h3>
    <p class="abs card-copy">Sed ut perspiciatis unde omnis iste natus error sit voluptatem tium</p>
    <a class="abs card-more">READ MORE</a>
  </article>
</section>

<section class="abs banner" role="img" aria-label="Photo of an audience smiling and applauding at an event">
  <h2 class="abs banner-title">BRIGHT GATHERING</h2>
  <p class="abs banner-copy">Lorem ipsum dolor sit amet, consectetur adipiscing elit, sed do eiusmod tempor incididunt ut labore et dolore magna aliqua. Quis ipsum suspendisse ultrices gravida.</p>
  <a class="abs btn btn-orange" style="left:91px;top:244px;width:186px;height:52px;font-size:17px">Register Now <span class="arrow"></span></a>
</section>

<section>
  <h2 class="abs center promo-name">BRIGHT GATHERINGS</h2>
  <p class="abs promo-copy" style="text-align:center">Lorem ipsum dolor sit amet, consectetur adipiscing elit, sed do eiusmod tempor incididunt ut labore et dolore magna aliqua. Quis ipsum suspendisse ultrices gravida.</p>
  <a class="abs btn btn-orange" style="left:484px;top:3020px;width:232px;height:53px;font-size:17px">Get the Book Now <span class="arrow"></span></a>

  <div class="abs orbit"></div>
  <div class="abs core"><div class="abs core-book" role="img" aria-label="Bright Gatherings book cover mockup"></div></div>

  <div class="abs feature" style="left:315px;top:3179px">
    <span style="color:#fff;font-size:60px;font-weight:800">$</span>
  </div>
  <div class="abs feature" style="left:765px;top:3179px">
    <svg width="56" height="50" viewBox="0 0 56 50" aria-hidden="true"><rect x="4" y="16" width="48" height="12" fill="#fff"/><rect x="8" y="30" width="40" height="18" fill="#fff"/><rect x="25" y="16" width="6" height="32" fill="#f15a0f"/><circle cx="20" cy="10" r="6" fill="none" stroke="#fff" stroke-width="4"/><circle cx="36" cy="10" r="6" fill="none" stroke="#fff" stroke-width="4"/></svg>
  </div>
  <div class="abs feature" style="left:315px;top:3510px">
    <svg width="60" height="46" viewBox="0 0 60 46" aria-hidden="true"><path d="M2 6 Q16 0 28 6 V44 Q16 38 2 44Z" fill="#fff"/><path d="M58 6 Q44 0 32 6 V44 Q44 38 58 44Z" fill="#fff"/></svg>
  </div>
  <div class="abs feature" style="left:765px;top:3510px">
    <svg width="60" height="52" viewBox="0 0 60 52" aria-hidden="true"><path d="M4 4 H56 L58 18 H2Z" fill="#fff"/><rect x="6" y="22" width="48" height="28" fill="#fff"/><rect x="14" y="30" width="12" height="20" fill="#f15a0f"/><rect x="32" y="30" width="14" height="10" fill="#f15a0f"/></svg>
  </div>

  <p class="abs feature-label" style="left:79px;top:3203px">Just<span>$15.97</span></p>
  <p class="abs feature-label" style="left:914px;top:3203px">See<span>Our Deals</span></p>
  <p class="abs feature-label" style="left:79px;top:3543px">look<span>Inside</span></p>
  <p class="abs feature-label" style="left:914px;top:3543px">Our<span>Merchandise</span></p>
</section>

<div class="abs footer-edge"></div>
<footer class="abs footer">
  <p class="abs center footer-name">BRIGHT GATHERINGS</p>
  <div class="abs footer-dots" aria-label="Social profiles"><span></span><span></span><span></span><span></span></div>
  <p class="abs center footer-links">Home &nbsp;|&nbsp; About &nbsp;|&nbsp; Blog &nbsp;|&nbsp; Podcasts &nbsp;|&nbsp; Training &nbsp;|&nbsp; Free Stuff &nbsp;|&nbsp; Webinars &nbsp;|&nbsp; Shop</p>
  <p class="abs center copyright">Copyright &copy; 2019. All Rights Reserved.</p>
</footer>

</body>
</html>
```